holloway paving service

Needs to have phone number 0418259730 and email markholloway@brightmail.com.au.
ABN 62318470915
name mark holloway

For all your concreting solutions
Excavation
Exposed & colour concrete
House & shed slabs
Driveways
Landing & steps

Contact Information for Business Card

ph 0418259730
email markholloway@brightmail.com.au.
ABN 62318470915
name mark holloway

```html
<!DOCTYPE html>
<html lang="en">
<head>
<meta charset="utf-8">
<title>Holloway Paving Service – Business Card</title>
<link href="https://fonts.googleapis.com/css2?family=Open+Sans:wght@400;600;700&display=swap" rel="stylesheet">
<style>
  :root {
    --orange: #ec6a1f;
    --white: #fbfbfa;
    --charcoal: #5f6062;
    --shadow-grey: #8c8d8f;
    --rule-grey: #d9d9d9;
    --light-text: #e8e8e8;
    --page: #e7e5e1;
  }
  * { box-sizing: border-box; margin: 0; padding: 0; }
  html, body { width: 1200px; height: 886px; overflow: hidden; }
  body {
    background: var(--page);
    font-family: "Open Sans", Arial, sans-serif;
    position: relative;
  }
  .card {
    position: absolute;
    top: 288px;
    width: 540px;
    height: 309px;
    overflow: hidden;
    box-shadow: 0 6px 18px rgba(0,0,0,.18);
  }
  .card-front { left: 40px; background: var(--orange); }
  .card-back  { left: 620px; background: var(--charcoal); }

  .front-shape { position: absolute; inset: 0; }

  .holder-name {
    position: absolute; left: 30px; top: 44px;
    color: var(--white); font-weight: 700; font-size: 21px;
    letter-spacing: .5px; text-transform: uppercase;
    white-space: nowrap;
  }
  .contact-list {
    position: absolute; left: 30px; bottom: 28px;
    list-style: none; color: var(--white); font-size: 11.5px; line-height: 20px;
    white-space: nowrap;
  }
  .contact-list li { display: flex; align-items: center; gap: 7px; }
  .contact-list svg { width: 10px; height: 10px; flex: none; }
  .contact-list .abn { padding-left: 17px; }

  .brand-block {
    position: absolute; left: 338px; top: 118px;
    display: flex; align-items: center; gap: 12px;
  }
  .brand-mark { width: 22px; height: 22px; background: var(--orange); flex: none; }
  .brand-divider { width: 1px; height: 58px; background: var(--orange); }
  .brand-name {
    color: var(--orange); font-weight: 700; font-size: 13px;
    line-height: 16px; text-transform: uppercase; width: 130px;
  }
  .brand-phone { color: var(--orange); font-size: 12px; font-weight: 600; margin-top: 3px; }

  .back-deco {
    position: absolute; left: 150px; top: -40px;
    width: 190px; height: 190px;
    background: rgba(236,106,31,.22);
  }
  .back-brand { position: absolute; left: 36px; bottom: 46px; }
  .back-brand .brand-name { font-size: 17px; line-height: 21px; width: 200px; }
  .back-brand .rule { width: 150px; height: 2px; background: var(--rule-grey); margin: 8px 0 6px; }
  .back-brand .brand-phone { font-size: 14px; }
  .website {
    color: var(--light-text); font-size: 12px; letter-spacing: 3.5px; margin-top: 4px;
    white-space: nowrap;
  }
  .service-list {
    position: absolute; right: 34px; bottom: 44px;
    list-style: none; text-align: right;
    color: var(--white); font-size: 13px; line-height: 20px;
  }
  .service-list li::after {
    content: ""; display: inline-block; width: 5px; height: 5px;
    background: var(--orange); border-radius: 50%;
    margin-left: 9px; vertical-align: middle;
  }
</style>
</head>
<body>

  <section class="card card-front" aria-label="Business card front">
    <svg class="front-shape" viewBox="0 0 540 309" aria-hidden="true">
      <polygon points="346,0 540,0 540,309 351,309 195,140" fill="var(--shadow-grey)" transform="translate(5,9)"/>
      <polygon points="346,0 540,0 540,309 351,309 195,140" fill="var(--white)"/>
    </svg>

    <h1 class="holder-name">Mark Holloway</h1>

    <ul class="contact-list">
      <li>
        <svg viewBox="0 0 24 24"><path fill="#fff" d="M6.6 10.8a15.1 15.1 0 0 0 6.6 6.6l2.2-2.2a1 1 0 0 1 1-.25 11.4 11.4 0 0 0 3.6.57 1 1 0 0 1 1 1V20a1 1 0 0 1-1 1A17 17 0 0 1 3 4a1 1 0 0 1 1-1h3.5a1 1 0 0 1 1 1c0 1.25.2 2.45.57 3.6a1 1 0 0 1-.25 1z"/></svg>
        0418259730
      </li>
      <li>
        <svg viewBox="0 0 24 24"><rect x="2" y="5" width="20" height="14" rx="2" fill="#fff"/><path d="M3 6l9 7 9-7" stroke="var(--orange)" stroke-width="2" fill="none"/></svg>
        markholloway@brightmail.com.au
      </li>
      <li>
        <svg viewBox="0 0 24 24"><circle cx="12" cy="12" r="10" fill="#fff"/><circle cx="12" cy="12" r="4" fill="var(--orange)"/></svg>
        www.hollowaypaving.com.au
      </li>
      <li class="abn">ABN 62318470915</li>
    </ul>

    <div class="brand-block">
      <span class="brand-mark"></span>
      <span class="brand-divider"></span>
      <div>
        <div class="brand-name">Holloway Paving Service</div>
        <div class="brand-phone">0418259730</div>
      </div>
    </div>
  </section>

  <section class="card card-back" aria-label="Business card back">
    <span class="back-deco" aria-hidden="true"></span>

    <div class="back-brand">
      <div class="brand-name">Holloway Paving Service</div>
      <div class="rule"></div>
      <div class="brand-phone">0418259730</div>
      <div class="website">www.hollowaypaving.com.au</div>
    </div>

    <ul class="service-list">
      <li>Excavation</li>
      <li>Exposed &amp; colour concrete</li>
      <li>House &amp; shed slabs</li>
      <li>Driveways</li>
      <li>Landing &amp; steps</li>
    </ul>
  </section>

</body>
</html>
```